Business Card Design Competition

We need a business card design for our Internet Marketing company. We require both front and back designs and the final card must be 89x53mm in size, plus crop marks to 91x55mm. Colours as per logo, plus perhaps black and/or grey (#828282).
Final text must be editable (if you can supply an editable Fireworks PNG, even better)...
FRONT TEXT:
Full Name
Position
Address Line
Suburb, State, Postcode
Phone: 0000 000 000
Mobile: 0000 000 000
Email: xxx@brightlanemedia.com.au
Web: www.brightlanemedia.com.au
Rear of card should be a fresh design plus our slogan text: "Getting You Noticed" in large font, then in small text "Kestrel Holdings Pty Ltd (ABN: 42 561 903 774)".
Target Market(s)
Small/Medium Businesses
Industry/Entity Type
Business

```html
<!DOCTYPE html>
<html lang="en">
<head>
<meta charset="utf-8">
<title>Brightlane Media – Business Card</title>
<link rel="stylesheet" href="https://fonts.googleapis.com/css2?family=Arimo:wght@400&display=swap">
<style>
  :root {
    --brand-orange: #f7941d;
    --brand-green: #8cc63f;
    --band-green: #c9e1a2;
    --card-edge: #9a9a9a;
    --ink: #333333;
    --page: #ffffff;
  }
  html, body {
    margin: 0;
    padding: 0;
    width: 970px;
    height: 1200px;
    overflow: hidden;
    background: var(--page);
    font-family: "Arimo", Arial, sans-serif;
  }
  .sheet {
    position: relative;
    width: 970px;
    height: 1200px;
  }
  .card {
    position: absolute;
    left: 6px;
    width: 956px;
    background: #fff;
    border: 2px solid var(--card-edge);
    border-radius: 34px;
    overflow: hidden;
    box-shadow: 0 3px 6px rgba(0, 0, 0, 0.18);
  }
  .card--front { top: 6px; height: 570px; }
  .card--back  { top: 598px; height: 578px; }
  .card__band {
    position: absolute;
    left: 0;
    right: 0;
    bottom: 0;
    height: 54px;
    background: var(--band-green);
  }
  .card--back .card__band { height: 48px; }

  .brand {
    position: absolute;
    left: 36px;
    top: 118px;
    display: flex;
    align-items: center;
    gap: 36px;
  }
  .brand__mark {
    width: 260px;
    height: 260px;
    flex: none;
  }
  .brand__name {
    margin: 0;
    font-weight: 400;
    font-size: 96px;
    line-height: 1.05;
    color: var(--brand-orange);
    letter-spacing: 1px;
  }

  .contact {
    position: absolute;
    left: 94px;
    top: 48px;
    color: var(--ink);
    font-size: 32px;
    line-height: 36px;
  }
  .contact__group { margin: 0; }
  .contact__group + .contact__group { margin-top: 41px; }
  .contact__group--web { margin-top: 46px !important; }
</style>
</head>
<body>
<main class="sheet">
  <section class="card card--front" aria-label="Card front">
    <div class="brand">
      <svg class="brand__mark" viewBox="0 0 260 260" aria-hidden="true">
        <circle cx="130" cy="130" r="128" fill="var(--brand-orange)"/>
      </svg>
      <p class="brand__name">Brightlane<br>Media</p>
    </div>
    <div class="card__band"></div>
  </section>

  <section class="card card--back" aria-label="Card back">
    <div class="contact">
      <p class="contact__group">Full Name<br>Position</p>
      <p class="contact__group">Address Line<br>Suburb, State, Postcode</p>
      <p class="contact__group">Phone: 0000 000 000<br>Mobile: 0000 000 000</p>
      <p class="contact__group contact__group--web">Email: xxx@brightlanemedia.com.au<br>Web: www.brightlanemedia.com.au</p>
    </div>
    <div class="card__band"></div>
  </section>
</main>
</body>
</html>
```